Web Design Project for Communications Agency

The design I need (PSD file) is for an agency offering specialised PR and communications services for customers in the healthcare sector.

OBJECTIVES OF THE WEBSITE:
1. To promote the agency's communication services
2. To position Solène Brivard as an industry leader, an expert in healthcare PR and communications by highlighting blogposts and social media.

WHAT I NEED:
1st, I need the design for the Home Page ONLY.
Once approved, I will need the other pages designed as well. (Here is prototype that we've already developed for the Website that will guide you in the design:
http://qorvelle.net/solenebrivard/)

VISUAL INSPIRATION
We want to give this Website a "Flat Design" look. Here are some websites for inspiration :
- http://tavrolinkworks.com/#!/process
- http://www.brindlemoss.co/
- http://quellaroft.com/

Also, reuse images found on the company's current Website :
http://www.solenebrivard.com/fr/index.html

HOMEPAGE MAIN ELEMENTS:
1. Main menu : 6 sections
Accueil | Agence | Services | Approche | Publications | Contact

2. Main Call To Action (big dark rectangle in prototype):
Can be slider or just an information bloc.

3. Publications récentes :
The 4 latest blog posts must be features on the homepage (will be linked with the "Publications" section)

4. Dynamic Footer :
Contains a Chirpline feed and a Subscribe to our Newsletter feature (revecez nos publications)

OTHER PAGES (to design once Homepage is approved)
- Agence (about us)
- Services (our team)
- Approche (our approach)
- Publications (blog articles)
- Contact (Contact us)

Industry/Entity Type

Communications

Requirements
Must have
• Please refer to prototype :
http://qorvelle.net/solenebrivard/
Must have ALL features present in prototype.

Also, must reuse this picture in the design : http://solenebrivard.com/static/images/home-big-box.jpg

Finally, you will find attached the company logo.

```html
<!DOCTYPE html>
<html lang="fr">
<head>
<meta charset="utf-8">
<title>Solène Brivard — Cabinet-conseil santé</title>
<link rel="stylesheet" href="https://fonts.googleapis.com/css2?family=Arvo:wght@400;700&family=Arimo:wght@400;700&family=Lato:wght@300;400;700&family=Open+Sans:wght@400;600&display=swap">
<style>
:root{
  --header:#3b3b3b;
  --accent:#d8333f;
  --accent-soft:#f0605c;
  --page:#efefef;
  --footer:#2b2b2b;
  --footer-deep:#232323;
  --field:#444444;
  --ink:#444444;
  --light:#bdbdbd;
  --white:#ffffff;
  --sky:#2bb6ea;
}
*{box-sizing:border-box;margin:0;padding:0}
html,body{width:714px;height:1200px;overflow:hidden}
body{font-family:"Lato",sans-serif;background:var(--page);position:relative}

.site-header{position:absolute;left:0;top:0;width:714px;height:66px;background:var(--header);border-bottom:2px solid var(--accent)}
.brand{position:absolute;left:76px;top:22px;display:flex;align-items:center;gap:7px;color:var(--accent);font-family:"Lato",sans-serif;font-weight:700;font-size:17px}
.brand-dot{width:9px;height:9px;background:var(--accent);border-radius:50%}
.main-nav{position:absolute;right:71px;top:27px;display:flex;gap:20px}
.main-nav a{color:var(--white);text-decoration:none;font-family:"Open Sans",sans-serif;font-size:10px}

.hero{position:absolute;left:0;top:66px;width:714px;height:376px;
  background:linear-gradient(180deg,#cfd2d2 0%,#dfe0de 18%,#e9e5d6 34%,#e4dcc1 48%,#c99d68 58%,#d9cfb4 64%,#34458a 70%,#4f67a8 75%,#7a96cf 84%,#9db2dc 93%,#8aa2d2 100%)}
.hero-box{position:absolute;left:66px;top:69px;width:583px;height:129px;background:rgba(240,240,240,.82);text-align:center}
.hero-title{margin-top:25px;font-family:"Arvo",serif;font-size:18.5px;line-height:24px;color:#4a4a4a;font-weight:400}
.hero-cta{display:inline-block;margin-top:11px;padding:4px 11px;background:var(--accent);color:var(--white);font-family:"Arvo",serif;font-weight:700;font-size:11.5px}

.publications{position:absolute;left:0;top:442px;width:714px;height:416px}
.section-title{position:absolute;left:0;width:714px;top:34px;text-align:center;font-family:"Arimo",sans-serif;font-size:30px;color:var(--ink);font-weight:400}
.pub{position:absolute;width:190px;height:125px}
.pub-1{left:66px;top:111px;background:linear-gradient(135deg,#cdb9ae 0%,#e6dcd6 45%,#f2eeeb 100%)}
.pub-2{left:262px;top:111px;background:linear-gradient(160deg,#5a7cc6 0%,#8ea8dd 40%,#c5d3ef 70%,#e6ecf7 100%)}
.pub-3{left:459px;top:111px;background:radial-gradient(circle at 50% 40%,#f1eeea 0%,#d9d2c8 32%,#c98f52 60%,#b7773d 100%)}
.pub-4{left:66px;top:241px;background:linear-gradient(100deg,#f3f1ee 0%,#e8d6c8 40%,#f4f3f1 60%,#cdb9a8 100%)}
.pub-5{left:262px;top:241px;background:linear-gradient(180deg,#bfd4ea 0%,#dce6ef 40%,#e9ecee 65%,#d8d4cb 100%)}
.pub-6{left:459px;top:241px;background:radial-gradient(circle at 50% 42%,#5f86bd 0%,#9db7d8 28%,#e6ecf3 52%,#d7a98a 78%,#c6916e 100%)}
.pub-overlay{position:absolute;left:6px;top:6px;width:177px;height:113px;background:rgba(216,51,63,.86);color:var(--white);text-align:center}
.pub-overlay h3{margin-top:48px;font-family:"Lato",sans-serif;font-weight:400;font-size:13px}
.pub-overlay p{font-size:7.5px;margin-top:1px}
.pub-plus{position:absolute;right:6px;bottom:6px;width:15px;height:15px;border-radius:50%;background:var(--accent);display:flex;align-items:center;justify-content:center}
.pub-plus svg{width:7px;height:7px;stroke:var(--white);stroke-width:2}

.site-footer{position:absolute;left:0;top:858px;width:714px;height:304px;background:var(--footer);color:var(--light)}
.touch-title{position:absolute;left:0;width:714px;top:13px;text-align:center;font-family:"Arimo",sans-serif;font-weight:700;font-size:16px;color:var(--white)}
.touch-lead{position:absolute;left:76px;width:562px;top:41px;text-align:center;font-size:10px;font-weight:300;line-height:15px;color:#aaa}
.newsletter-title{position:absolute;left:78px;top:92px;font-family:"Arimo",sans-serif;font-size:11.5px;color:var(--white)}
.field{position:absolute;left:78px;width:347px;height:19px;background:var(--field);font-size:7.5px;color:#999;padding:5px 5px}
.field-name{top:120px}.field-mail{top:148px}
.submit{position:absolute;left:78px;top:181px;width:49px;height:17px;background:var(--accent-soft);color:var(--white);font-size:5.5px;font-weight:700;letter-spacing:.5px;text-align:center;line-height:17px;border-radius:2px}
.col{position:absolute;top:218px;font-size:7px;line-height:12px;color:#aaa}
.col h4{font-family:"Arimo",sans-serif;font-size:10.5px;color:var(--white);margin-bottom:8px}
.col-address{left:80px;width:160px}
.col-elsewhere{left:254px;width:170px}
.contact-line{display:flex;align-items:center;gap:5px;margin-left:2px}
.contact-line svg{width:6px;height:6px;fill:var(--accent)}
.social{display:flex;gap:4px;margin-top:9px}
.social span{width:15px;height:15px;border-radius:50%}
.feed{position:absolute;left:444px;top:118px;width:200px}
.feed-name{font-family:"Lato",sans-serif;font-weight:700;font-size:40px;line-height:48px;color:var(--sky)}
.tweet{font-family:"Arimo",sans-serif;font-size:6.8px;line-height:10.5px;color:#aaa;margin-top:12px}
.tweet a{color:var(--accent);text-decoration:none}
.tweet+.tweet{margin-top:9px}

.bottom-bar{position:absolute;left:0;top:1162px;width:714px;height:38px;background:var(--footer-deep);text-align:center;font-size:7px;line-height:38px;color:#999}
.bottom-bar strong{color:#ddd;font-weight:400}
</style>
</head>
<body>

<header class="site-header">
  <div class="brand"><span class="brand-dot"></span>Solène Brivard</div>
  <nav class="main-nav">
    <a href="#">Accueil</a><a href="#">Agence</a><a href="#">Services</a><a href="#">Approche</a><a href="#">Publications</a><a href="#">Contact</a>
  </nav>
</header>

<section class="hero" role="img" aria-label="Couloir d'hôpital lumineux, plafond blanc, murs crème, plancher bleu, avec un cube blanc orné d'une croix rouge">
  <div class="hero-box">
    <h1 class="hero-title">Cabinet-conseil en communications et affaires publiques<br>spécialisé dans le secteur de la santé.</h1>
    <span class="hero-cta">En Savior Plus</span>
  </div>
</section>

<section class="publications">
  <h2 class="section-title">Publication Récentes</h2>
  <article class="pub pub-1" role="img" aria-label="Photo de publication : professionnel de la santé">
    <div class="pub-overlay">
      <h3>Titre de la publication</h3>
      <p>Dolore eu feugiat nulla</p>
      <span class="pub-plus"><svg viewBox="0 0 10 10"><path d="M5 0v10M0 5h10"/></svg></span>
    </div>
  </article>
  <article class="pub pub-2" role="img" aria-label="Photo de publication : stéthoscope sur un clavier bleu"></article>
  <article class="pub pub-3" role="img" aria-label="Photo de publication : pèse-personne en forme d'horloge sur fond de bois"></article>
  <article class="pub pub-4" role="img" aria-label="Photo de publication : médecin auscultant une enfant"></article>
  <article class="pub pub-5" role="img" aria-label="Photo de publication : famille courant sur une plage"></article>
  <article class="pub pub-6" role="img" aria-label="Photo de publication : globe de verre bleu dans une main"></article>
</section>

<footer class="site-footer">
  <h2 class="touch-title">Get In Touch</h2>
  <p class="touch-lead">Maecenas sed diam eget risus varius. Risus varius blandit sit amet non magna. Duis mollis, est non commodo luctus, nisi erat porttitor ligula, eget lacinia odio sem nec elit. Sed posuere consectetur est at lobortis.</p>

  <h3 class="newsletter-title">Recevez nos publications</h3>
  <div class="field field-name">Votre nom</div>
  <div class="field field-mail">Votre courriel</div>
  <div class="submit">SUBMIT</div>

  <div class="col col-address">
    <h4>Address</h4>
    <p>Fusce dapibus, tellus commodo, tortor mauris</p>
    <p class="contact-line"><svg viewBox="0 0 10 10"><path d="M5 0a3.5 3.5 0 0 1 3.5 3.5C8.5 6 5 10 5 10S1.5 6 1.5 3.5A3.5 3.5 0 0 1 5 0z"/></svg>Lune St. 22/07 Clair, Saturne</p>
    <p class="contact-line"><svg viewBox="0 0 10 10"><path d="M2 0l2 2.5-1 1.5a6 6 0 0 0 3 3l1.5-1L10 8l-1.5 2C4 10 0 6 0 1.5z"/></svg>0312 408 27 19</p>
    <p class="contact-line"><svg viewBox="0 0 10 10"><path d="M0 2h10v6H0z"/></svg>bonjour@brivard.net</p>
  </div>

  <div class="col col-elsewhere">
    <h4>Elsewhere</h4>
    <p>Sed posuere consectetur est at lobortis. Morbi leo risus, porta ac consectetur malesuada magna.</p>
    <div class="social">
      <span style="background:#f08a1c"></span><span style="background:#3aa9dd"></span><span style="background:#3d64c4"></span><span style="background:#e66aa6"></span><span style="background:#d8333f"></span><span style="background:#9a6b55"></span><span style="background:#1ab0d8"></span>
    </div>
  </div>

  <div class="feed">
    <div class="feed-name">Chirpline</div>
    <p class="tweet">Dolore eu feugiat nulla facilisis at vero eros et accumsan et iusto odio dignissim qui blandit praesent <a href="#">@luptatum zzril delenit augue duis dolore</a></p>
    <p class="tweet">Dolore eu feugiat nulla facilisis at vero eros et accumsan et iusto odio dignissim qui blandit praesent <a href="#">@luptatum zzril delenit augue duis dolore</a></p>
    <p class="tweet">Dolore eu feugiat nulla facilisis at vero eros et accumsan et iusto odio dignissim qui blandit praesent <a href="#">@luptatum zzril delenit augue duis dolore</a></p>
  </div>
</footer>

<div class="bottom-bar">© 2013 <strong>Solène Brivard</strong> All rights reserved. Theme by Velorane.</div>

</body>
</html>
```